Business Card Design

It's an investment advisory service for individuals with all there investment needs. Also financial consulting to businesses and governmental agencies on retirement plans etc. It's personalized not commoditized help. Should show strength, knowledge and money orientation.

Reason: Will be out of town setting up office.

Reason: waiting for the 2/3rds of group to vote

Reason: only half the votes are in, I'm calling and getting verbals, but at this time we are down to 2 designs.

Industry/Entity Type

Investment

Contact Information for Business Card

B. Rel K. Financial Consulting and Wealth Management, Berislav Mike Holcek, 5172 Pasadena Loma Verde, San Diego, CA 94417-6381, Registered Investment Advisor

Requirements
Nice to have
• Something money oriented

```html
<!DOCTYPE html>
<html lang="en">
<head>
<meta charset="utf-8">
<title>B. Rel K. Financial Consulting – Business Card</title>
<link href="https://fonts.googleapis.com/css2?family=Andika:wght@700&family=Bree+Serif&family=Lato:wght@400&display=swap" rel="stylesheet">
<style>
  :root {
    --page: #eceae4;
    --cream: #fdf9d2;
    --stripe-yellow: #f4ea2a;
    --stripe-orange: #f0a21c;
    --ink-green: #0f7a36;
    --ink-blue: #1d2f9c;
    --ink-dark: #2b2b2b;
  }
  * { margin: 0; padding: 0; box-sizing: border-box; }
  html, body { width: 1200px; height: 900px; overflow: hidden; }
  body { background: var(--page); position: relative; }

  .card {
    position: absolute;
    left: 120px; top: 176px;
    width: 960px; height: 548px;
    background: var(--cream);
    overflow: hidden;
    box-shadow: 0 6px 24px rgba(0,0,0,.18);
  }
  .card-bands { position: absolute; inset: 0; }

  .brand-name {
    position: absolute; left: 36px; top: 36px;
    font-family: "Lato", sans-serif; font-weight: 400;
    font-size: 30px; color: var(--cream);
  }

  .advisor-name {
    position: absolute; right: 30px; top: 104px;
    font-family: "Bree Serif", serif; font-size: 34px;
    color: var(--ink-blue);
  }

  .firm {
    position: absolute; left: 150px; top: 238px;
    font-family: "Andika", sans-serif; font-weight: 700;
    font-size: 36px; line-height: 1.15; color: var(--ink-green);
  }
  .firm-role {
    display: block; margin-top: 2px;
    font-family: "Lato", sans-serif; font-weight: 400;
    font-size: 27px; color: var(--ink-dark);
  }

  .address {
    position: absolute; left: 28px; top: 452px;
    font-family: "Lato", sans-serif; font-size: 21px;
    line-height: 1.5; color: var(--ink-dark);
  }
  .address-line { display: flex; align-items: center; gap: 8px; }
  .address-line svg { width: 16px; height: 20px; flex: none; }

  .money-tree {
    position: absolute; left: 700px; top: 300px;
    width: 190px; height: 210px;
    border-radius: 50% 50% 18px 18px;
    background: radial-gradient(circle at 50% 40%, #e8efa0 0%, #a9d86a 55%, #7fbf4f 100%);
  }
</style>
</head>
<body>
  <div class="card">
    <svg class="card-bands" viewBox="0 0 960 548" preserveAspectRatio="none" aria-hidden="true">
      <defs>
        <linearGradient id="topGreen" x1="0" y1="0" x2="1" y2="0">
          <stop offset="0" stop-color="#9fdc5a"/>
          <stop offset="1" stop-color="#2f9e2f"/>
        </linearGradient>
        <linearGradient id="bottomGreen" x1="0" y1="0" x2="1" y2="1">
          <stop offset="0" stop-color="#2f9e2f"/>
          <stop offset="1" stop-color="#6cc93f"/>
        </linearGradient>
      </defs>
      <path d="M0,0 H960 V304 C660,274 380,54 0,28 Z" fill="var(--stripe-orange)"/>
      <path d="M0,0 H960 V290 C660,260 380,40 0,14 Z" fill="url(#topGreen)"/>
      <path d="M0,392 C320,436 660,478 960,490 V548 H0 Z" fill="var(--stripe-yellow)"/>
      <path d="M0,406 C320,450 660,492 960,504 V548 H0 Z" fill="url(#bottomGreen)"/>
    </svg>

    <div class="brand-name">B. Rel K.</div>

    <div class="advisor-name">Berislav Mike Holcek</div>

    <div class="firm">
      B. Rel K. Financial Consulting<br>
      &amp; Wealth Management
      <span class="firm-role">Registered Investment Advisor</span>
    </div>

    <div class="money-tree" role="img" aria-label="Illustration of a money tree with gold coins among green leaves"></div>

    <div class="address">
      <div class="address-line">
        <svg viewBox="0 0 16 20"><path d="M8 0a7 7 0 0 0-7 7c0 5 7 13 7 13s7-8 7-13a7 7 0 0 0-7-7zm0 10a3 3 0 1 1 0-6 3 3 0 0 1 0 6z" fill="var(--ink-dark)"/></svg>
        5172 Pasadena Loma Verde, San Diego, CA
      </div>
      <div class="address-line">
        <svg viewBox="0 0 16 20"><path d="M3 2l3-1 2 5-2 1.5c1 2.5 2.5 4 5 5L12.5 10l2.5 1-.5 4c-1 1-3 1.5-6-.5S2.5 8 2 5c-.2-1.4.2-2.4 1-3z" fill="var(--ink-dark)"/></svg>
        94417-6381,
      </div>
    </div>
  </div>
</body>
</html>
```